Volbrey Inc Business Card

Looking to get an updated business card for a Contract Machining company (www.volbreyinc.example) - looking for a clean design the portrays the technical nature of the business - colors can follow the website design and be in any combination that makes sense (red black, white, metallic or silver) - logos attached for use also. Would like space for: Name, title, business phone (555 214-3086), cell phone , website (www.volbreyinc.example) - possibly QR code could be integrated for website (designer choice), business address - 418 Harlow Bend, Brinmoor, WA 98199 (cards will be for 4 employees, I will either need to modify a template or I can provide individual information)
Target Market(s)
Aerospace, defense and medical device manufacturing companies that need machining
Industry/Entity Type
Machining for aerospace, defense, medical
Contact Information for Business Card
Name, Title, Business Phone, Cell Phone, email, business website and business address
Look and feel

```html
<!DOCTYPE html>
<html lang="en">
<head>
<meta charset="utf-8">
<title>Volbrey Inc Business Card</title>
<link href="https://fonts.googleapis.com/css2?family=Montserrat:wght@400;500;700&display=swap" rel="stylesheet">
<style>
  :root {
    --bg: #e6e4e2;
    --card-black: #1f1f20;
    --card-black-light: #2c2c2e;
    --brand-red: #c8313c;
    --edge-red: #a3232c;
    --text-white: #f2f2f2;
    --silver: #bdbdbd;
  }
  * { margin: 0; padding: 0; box-sizing: border-box; }
  html, body { width: 1200px; height: 716px; overflow: hidden; }
  body {
    background: var(--bg);
    font-family: "Montserrat", sans-serif;
    display: flex;
    align-items: center;
    justify-content: center;
    gap: 40px;
  }
  .card {
    position: relative;
    width: 520px;
    height: 297px;
    border-radius: 4px;
    border: 2px solid var(--edge-red);
    overflow: hidden;
    box-shadow: 0 10px 24px rgba(0,0,0,0.25);
  }
  .card-back {
    background: linear-gradient(120deg, #0e0e0f 0%, #1b1b1c 35%, #5a5a5b 62%, var(--silver) 82%, #7c7c7d 100%);
  }
  .back-pattern { position: absolute; inset: 0; }
  .back-name {
    position: absolute;
    left: 50%;
    top: 72%;
    transform: translate(-50%, -50%);
    color: var(--brand-red);
    font-weight: 700;
    font-size: 20px;
    letter-spacing: 1px;
  }
  .card-front {
    background: linear-gradient(110deg, var(--card-black-light) 0%, var(--card-black) 55%, #161617 100%);
  }
  .brand {
    position: absolute;
    left: 36px;
    top: 104px;
  }
  .brand-name {
    color: var(--brand-red);
    font-weight: 700;
    font-size: 46px;
    line-height: 1;
    letter-spacing: 0.5px;
  }
  .brand-suffix {
    color: var(--text-white);
    font-weight: 400;
    font-size: 20px;
    margin-top: 6px;
    margin-left: 4px;
  }
  .divider {
    position: absolute;
    left: 296px;
    top: 66px;
    width: 2px;
    height: 168px;
    background: var(--brand-red);
  }
  .contact {
    position: absolute;
    left: 314px;
    top: 70px;
    color: var(--text-white);
    font-size: 11.5px;
    line-height: 1.45;
  }
  .person-name {
    color: var(--brand-red);
    font-weight: 700;
    font-size: 16px;
    letter-spacing: 0.5px;
  }
  .person-title { font-weight: 500; font-size: 12px; margin-bottom: 4px; }
  .address { margin-bottom: 4px; }
  .contact-line { display: flex; align-items: center; gap: 6px; }
  .contact-line svg { width: 10px; height: 10px; flex: none; }
</style>
</head>
<body>
  <div class="card card-back">
    <div class="back-pattern" role="img" aria-label="Repeating brand pattern fading from black to metallic silver"></div>
    <span class="back-name">VOLBREY</span>
  </div>

  <div class="card card-front">
    <div class="brand">
      <div class="brand-name">VOLBREY</div>
      <div class="brand-suffix">INC.</div>
    </div>
    <div class="divider"></div>
    <div class="contact">
      <div class="person-name">DANIEL ORWELL</div>
      <div class="person-title">DIRECTOR</div>
      <div class="address">418 Harlow Bend,<br>Brinmoor, WA 98199</div>
      <div class="contact-line">
        <svg viewBox="0 0 10 10"><path d="M2 1 L4 3 L3 4 Q4 6 6 7 L7 6 L9 8 L8 9 Q3 9 1 2 Z" fill="none" stroke="var(--brand-red)" stroke-width="1"/></svg>
        555 214-3086
      </div>
      <div class="contact-line">
        <svg viewBox="0 0 10 10"><rect x="2.5" y="0.8" width="5" height="8.4" rx="1" fill="none" stroke="var(--brand-red)" stroke-width="1"/><circle cx="5" cy="7.6" r="0.6" fill="var(--brand-red)"/></svg>
        555-870-4419
      </div>
      <div class="contact-line">
        <svg viewBox="0 0 10 10"><rect x="0.8" y="2" width="8.4" height="6" fill="none" stroke="var(--brand-red)" stroke-width="1"/><path d="M1 2.3 L5 5.5 L9 2.3" fill="none" stroke="var(--brand-red)" stroke-width="1"/></svg>
        info@volbreyinc.example
      </div>
      <div class="contact-line">
        <svg viewBox="0 0 10 10"><circle cx="5" cy="5" r="4" fill="none" stroke="var(--brand-red)" stroke-width="1"/><ellipse cx="5" cy="5" rx="1.8" ry="4" fill="none" stroke="var(--brand-red)" stroke-width="0.8"/><path d="M1 5 H9" stroke="var(--brand-red)" stroke-width="0.8"/></svg>
        www.volbreyinc.example
      </div>
    </div>
  </div>
</body>
</html>
```